Sell the dream! Property investment proposal document

We are looking for a proposal document which outlines our vision for property development. The purpose of the document is to raise investment from investors - sell the dream!
Brief summary:
Kestrel Dwellings Developments, is an emerging New Zealand property investment company with a focus on providing unique property investment opportunities.
Our expertise and capabilities in architectural modular homes provide us with a remarkable advantage in tackling the development of properties that are typically considered challenging, remote, or uniquely positioned.
Our specialization in this niche sector of property development not only sets us apart from competitors, but also paves the way for lucrative investment opportunities in the New Zealand property market.
Feel free to use any images from www.kestreldwellings.co.nz
Target Market(s)
investors for a unique property development opportunity
Industry/Entity Type
luxury property development in unique locations throughout New Zealand
Colors
Designer to choose only greyscale colors for use in the design.
Look and feel

```html
<!DOCTYPE html>
<html lang="en">
<head>
<meta charset="utf-8">
<title>Kestrel Dwellings Developments – Investment Proposal Spreads</title>
<link href="https://fonts.googleapis.com/css2?family=Montserrat:wght@600;700&family=Inter:wght@300;400;500&display=swap" rel="stylesheet">
<style>
  :root{
    --canvas:#ffffff;
    --ink:#161616;
    --charcoal:#1b1b1b;
    --panel-dark:rgba(20,20,20,.55);
    --panel-brown:#2e2a28;
    --paper-light:#ececec;
    --text-light:#f2f2f2;
    --text-muted:#cfcfcf;
    --text-dark:#2a2a2a;
  }
  *{margin:0;padding:0;box-sizing:border-box}
  html,body{width:1200px;height:675px;overflow:hidden;background:var(--canvas)}
  body{position:relative;font-family:"Inter",Arial,sans-serif}
  .spread{position:absolute;width:440px;height:311px;overflow:hidden;background:var(--charcoal)}
  .spread--overview{left:150px;top:16px}
  .spread--origins{left:610px;top:16px}
  .spread--finance{left:150px;top:347px}
  .spread--cover{left:610px;top:347px}
  .photo{position:absolute}
  .heading{font-family:"Montserrat",Arial,sans-serif;font-weight:700;font-size:9.5px;line-height:1.2;letter-spacing:.14em;text-transform:uppercase;color:var(--text-light)}
  .body-copy{font-size:3.6px;line-height:1.55;color:var(--text-muted);text-align:justify}
  .body-copy p{margin-bottom:3.5px}
  .brand{font-family:"Inter",Arial,sans-serif;font-weight:400;color:var(--text-light)}
  .brand-foot{position:absolute;right:16px;bottom:7px;font-size:9px}
  .brand-tag{position:absolute;left:18px;bottom:9px;display:flex;align-items:center;gap:3px;font-size:4px;color:var(--text-light)}
  .brand-tag .square{width:4px;height:4px;background:var(--text-light)}
  .page-fold{position:absolute;top:0;bottom:0;width:1px;background:rgba(255,255,255,.08)}

  /* Overview */
  .overview-photo{inset:0;background:linear-gradient(180deg,#c9ccce 0%,#a9acae 28%,#3a3a3a 36%,#2a2a2a 62%,#8d8f8f 78%,#4b5046 100%)}
  .overview-panel{position:absolute;left:0;top:0;width:145px;height:100%;background:var(--panel-dark)}
  .overview-panel .heading{position:absolute;left:22px;top:60px}
  .overview-panel .body-copy{position:absolute;left:22px;top:97px;width:114px}
  .callout{position:absolute;left:250px;top:191px;width:135px;padding-left:4px;border-left:.6px solid var(--text-light);font-size:3.7px;line-height:1.65;color:var(--text-light)}
  .callout strong{font-weight:500}

  /* Origins */
  .origins-photo{inset:0;background:linear-gradient(180deg,#9aa4ab 0%,#b5bcc0 30%,#6f7466 48%,#5a5d4f 70%,#a49f93 100%)}
  .origins-panel{position:absolute;left:13px;top:109px;width:130px;height:202px;background:rgba(40,40,40,.45)}
  .origins-panel .heading{position:absolute;left:8px;top:6px}
  .origins-panel .body-copy{position:absolute;left:8px;top:39px;width:115px}
  .origins-col{position:absolute;top:109px;width:66px;height:202px;background:rgba(30,30,30,.55)}
  .origins-col .body-copy{position:absolute;left:3px;top:9px;width:60px;text-align:left;color:var(--text-light)}
  .origins-col .photo{left:0;right:0;bottom:0;height:108px;background:linear-gradient(180deg,#8a9399,#50524c 60%,#2b2b2b)}

  /* Finance */
  .advantage-photo{left:0;top:0;width:220px;height:149px;background:linear-gradient(180deg,#d9d6d0 0%,#c9ccce 20%,#8e949a 42%,#7d8368 60%,#6b6557 78%,#a89b86 90%,#3a3a3a 100%)}
  .advantage-page{position:absolute;left:0;top:149px;width:220px;height:162px;background:var(--paper-light)}
  .advantage-page .heading{position:absolute;left:19px;top:14px;color:var(--ink)}
  .advantage-page .body-copy{position:absolute;left:19px;top:46px;width:118px;color:var(--text-dark)}
  .advantage-page .brand-tag{left:19px;color:var(--ink)}
  .advantage-page .brand-tag .square{background:var(--ink)}
  .summary-panel{position:absolute;left:220px;top:0;width:159px;height:204px;background:var(--panel-brown)}
  .summary-panel .heading{position:absolute;left:13px;top:16px}
  .summary-panel .body-copy{position:absolute;left:13px;top:57px;width:118px}
  .summary-photo{left:220px;top:204px;width:159px;height:107px;background:linear-gradient(180deg,#6c6760 0%,#b8a891 40%,#5d5a55 62%,#2d2b29 100%)}
  .summary-strip{left:379px;top:0;width:61px;height:311px;background:linear-gradient(180deg,#3a3a3a,#262626 50%,#1b1b1b)}

  /* Cover */
  .spread--cover{background:var(--charcoal)}
  .cover-name{position:absolute;left:26px;top:70px;font-size:52px;line-height:1;letter-spacing:-.01em}
  .cover-foot{position:absolute;left:26px;top:233px;font-size:13px}
  .cover-tagline{position:absolute;left:160px;top:233px;font-family:"Inter",Arial,sans-serif;font-weight:500;font-size:4.2px;line-height:1.4;color:var(--text-light)}
  .cover-vertical{position:absolute;left:386px;top:38px;width:210px;height:60px;transform-origin:0 0;transform:translate(0,218px) rotate(-90deg);font-size:60px;line-height:60px;letter-spacing:-.02em;color:var(--text-light)}
  .cover-contact{position:absolute;left:362px;top:289px;font-weight:500;font-size:4.4px;line-height:1.5;color:var(--text-light)}
</style>
</head>
<body>

<section class="spread spread--overview">
  <div class="photo overview-photo" role="img" aria-label="Photograph of a dark timber-clad modular home with slatted screens, concrete base and native planting"></div>
  <div class="overview-panel">
    <h2 class="heading">Business<br>Overview</h2>
    <div class="body-copy">
      <p>Kestrel Dwellings Developments, is an emerging New Zealand property investment company with a focus on providing unique property investment opportunities.</p>
      <p>Our expertise and capabilities in architectural modular homes provide us with a remarkable advantage in tackling the development of properties that are typically considered challenging, remote, or uniquely positioned.</p>
      <p>As a company with 45 employees boasting a wealth of experience in handling complex architectural projects, we are well-equipped to navigate the demands of such ventures.</p>
      <p>This advantage allows us to not only execute projects efficiently but also to deliver exceptional results within condensed time frames.</p>
      <p>By capitalizing on our ability to develop difficult, remote, or one-of-a-kind properties swiftly, we offer investors a rare chance to engage in projects that promise exceptional profitability in the New Zealand property market.</p>
    </div>
  </div>
  <p class="callout">Our specialization in this niche sector of property development not only sets us apart from competitors, but also paves the way <strong>for lucrative investment opportunities in the New Zealand property market.</strong></p>
  <div class="brand-tag"><span class="square"></span><span>Kestrel</span></div>
  <span class="brand brand-foot">Kestrel</span>
</section>

<section class="spread spread--origins">
  <div class="photo origins-photo" role="img" aria-label="Photograph of a low timber pavilion home on a grassy coastal headland with trees and a sandy shore"></div>
  <div class="page-fold" style="left:220px"></div>
  <div class="origins-panel">
    <h2 class="heading">Business<br>Origins</h2>
    <div class="body-copy">
      <p>Kestrel Dwellings Developments was established with the goal of transforming the property investment market in New Zealand by introducing an innovative approach that centres on architectural modular designs and streamlined project timelines.</p>
      <p>Driven by our enthusiasm for architecture and real estate, we have expanded our successful business model to not only offer financial opportunities for investors but also to express our passion for high-end architectural design.</p>
    </div>
  </div>
  <div class="origins-col" style="left:225px">
    <div class="body-copy"><p>With a wealth of experience accumulated over the past six years in construction and the property market, we are pivoting to focus solely on our property development initiatives, presenting completed projects to the market in exclusive locations.</p></div>
    <div class="photo" role="img" aria-label="Photograph of a lounge chair inside a glazed room facing the sea"></div>
  </div>
  <div class="origins-col" style="left:298px">
    <div class="body-copy"><p>These projects will boast high-quality standards, meticulous attention to detail and landscaping, and creative design elements.</p></div>
    <div class="photo" role="img" aria-label="Photograph of a timber interior with a view to native bush"></div>
  </div>
  <div class="origins-col" style="left:370px;width:70px">
    <div class="body-copy"><p>By introducing completed properties into the market, we aim to reach a wider audience, catering to individuals who prefer ready-to-occupy homes over engaging in the design and construction process. This approach also simplifies the financing process for prospective buyers, as established properties are often preferred by financial lenders.</p></div>
    <div class="photo" role="img" aria-label="Photograph of a rocky coastline below a cliffside home"></div>
  </div>
  <div class="brand-tag"><span class="square"></span><span>Kestrel</span></div>
  <span class="brand brand-foot">Kestrel</span>
</section>

<section class="spread spread--finance">
  <div class="photo advantage-photo" role="img" aria-label="Photograph of a bright living room with floor-to-ceiling glazing overlooking green hills and a harbour"></div>
  <div class="advantage-page">
    <h2 class="heading">Competitive<br>Advantage</h2>
    <div class="body-copy">
      <p>Our competitive advantage lies in the uniqueness of our property investment opportunities. Unlike traditional real estate companies, we focus on offering properties that are not only profitable but also aesthetically pleasing and unique. By catering to the tastes of architecture lovers, we set ourselves apart from the competition and attract a niche market of customers who appreciate the artistry and design of our projects.</p>
      <p>Additionally, the streamlined and condensed timelines facilitated by our modular approach provide quicker returns on investment.</p>
    </div>
    <div class="brand-tag"><span class="square"></span><span>Kestrel</span></div>
  </div>
  <div class="summary-panel">
    <h2 class="heading">Financial<br>Summary</h2>
    <div class="body-copy">
      <p>In terms of financial projections, with each development, we anticipate a profit of 10%–20% which will be project dependent.</p>
      <p>This growth is fuelled by the increasing demand for unique property investments in New Zealand and our ability to deliver high-quality services to the market in a condensed time frame, with heavily controlled costs.</p>
      <p>With a solid business model and a dedicated team, we are confident in our ability to achieve success and establish Kestrel Dwellings as a trusted name in the industry.</p>
      <p>New Zealand's property market has been experiencing steady growth over the years, making it an attractive destination for property investors. With its beautiful landscapes and strong economy, New Zealand offers a diverse range of investment opportunities for both local and international investors.</p>
      <p>The demand for quality properties in prime locations continues to rise, creating a favorable environment for property investment companies like ours that can lean on our modular benefits of being able to reach unique and remote locations.</p>
    </div>
  </div>
  <div class="photo summary-photo" role="img" aria-label="Photograph of a cantilevered glass pavilion above a pebble shore at sunset"></div>
  <div class="photo summary-strip" role="img" aria-label="Photograph of a dim interior with a lounge chair in black and white"></div>
  <span class="brand brand-foot">Kestrel</span>
</section>

<section class="spread spread--cover">
  <div class="page-fold" style="left:220px"></div>
  <span class="brand cover-name">Kestrel</span>
  <span class="brand cover-foot">Kestrel</span>
  <span class="cover-tagline">Modular<br>Architectural<br>Homes</span>
  <span class="brand cover-vertical">Kestrel</span>
  <p class="cover-contact">09 555 0147<br>sales@kestreldwellings.co.nz</p>
</section>

</body>
</html>
```